Business Card Design

We need a business card designed for our new company. Prefer a black card with white logo & writing.

Contact Information for Business Card

Ted Galloway, address: 7-4812 Fernhollow Road, Abbotsford, BC, V3K 8R2, Office Phone: 604-712-3390, Cell: 604-947-2164, Email: ted@resinworkshub.ca

Colors

Designer to choose only greyscale colors for use in the design.

```html
<!DOCTYPE html>
<html lang="en">
<head>
<meta charset="utf-8">
<title>Resinworks Hub — Business Card</title>
<link rel="stylesheet" href="https://fonts.googleapis.com/css2?family=Poppins:wght@300;400;500;700&display=swap">
<style>
  :root {
    --page: #e6e6e6;
    --card: #1f1f22;
    --card-back: #1b1b1e;
    --ink: #ffffff;
    --ink-soft: #d9d9d9;
    --rule: #8c8c8c;
    --pattern-a: #232327;
    --pattern-b: #2b2b30;
  }
  * { box-sizing: border-box; margin: 0; padding: 0; }
  html, body {
    width: 1200px; height: 780px; overflow: hidden;
    background: var(--page);
    font-family: "Poppins", sans-serif;
    color: var(--ink);
  }
  .sheet {
    position: relative; width: 1200px; height: 780px;
    display: flex; align-items: center; justify-content: center; gap: 40px;
  }
  .card {
    position: relative; width: 540px; height: 309px;
    background: var(--card); overflow: hidden;
    box-shadow: 0 10px 28px rgba(0,0,0,.25);
  }
  /* front */
  .edge-bar { position: absolute; width: 6px; background: var(--ink); }
  .edge-bar--left { left: 16px; top: 26px; height: 120px; }
  .edge-bar--right { right: 16px; bottom: 20px; height: 120px; }
  .brand {
    position: absolute; display: flex; align-items: center; gap: 10px;
    font-weight: 700; letter-spacing: .5px; line-height: 1;
  }
  .brand__square { width: 16px; height: 16px; background: var(--ink); flex: none; }
  .brand--front { left: 46px; top: 86px; font-size: 22px; flex-direction: column; align-items: flex-start; gap: 8px; }
  .brand--front .brand__row { display: flex; align-items: center; gap: 10px; }
  .divider { position: absolute; left: 0; top: 0; width: 540px; height: 309px; pointer-events: none; }
  .person { position: absolute; left: 312px; top: 82px; }
  .person__name { font-size: 30px; line-height: 1.05; font-weight: 300; white-space: nowrap; }
  .person__name strong { font-weight: 700; }
  .person__title { font-size: 13px; color: var(--ink-soft); margin-top: 4px; }
  .contacts { position: absolute; left: 290px; top: 150px; list-style: none; }
  .contacts li {
    display: flex; align-items: center; gap: 10px;
    font-size: 14px; line-height: 22px; font-weight: 400; color: var(--ink-soft);
  }
  .contacts svg { width: 13px; height: 13px; flex: none; }
  .address {
    position: absolute; left: 34px; bottom: 24px;
    font-size: 13.5px; color: var(--ink-soft); font-weight: 400;
  }
  /* back */
  .card--back { background: var(--card-back); }
  .backdrop {
    position: absolute; inset: 0;
    background: radial-gradient(circle at 70% 30%, var(--pattern-b), var(--pattern-a) 70%);
  }
  .brand--back {
    left: 50%; top: 50%; transform: translate(-50%, -50%);
    font-size: 34px; gap: 14px;
  }
  .brand--back .brand__square { width: 22px; height: 22px; }
</style>
</head>
<body>
<main class="sheet">
  <section class="card card--front" aria-label="Card front">
    <span class="edge-bar edge-bar--left"></span>
    <span class="edge-bar edge-bar--right"></span>

    <div class="brand brand--front">
      <div class="brand__row"><span class="brand__square"></span>RESINWORKS</div>
      <div class="brand__row">HUB</div>
    </div>

    <svg class="divider" viewBox="0 0 540 309" aria-hidden="true">
      <line x1="292" y1="60" x2="246" y2="250" stroke="var(--rule)" stroke-width="1"/>
    </svg>

    <div class="person">
      <p class="person__name"><strong>Ted</strong> Galloway</p>
      <p class="person__title">Founder &amp; CEO</p>
    </div>

    <ul class="contacts">
      <li>
        <svg viewBox="0 0 24 24" fill="none" stroke="#fff" stroke-width="2"><path d="M5 3h4l2 5-2.5 1.5a11 11 0 0 0 6 6L16 13l5 2v4a2 2 0 0 1-2 2A17 17 0 0 1 3 5a2 2 0 0 1 2-2z"/></svg>
        604-712-3390
      </li>
      <li>
        <svg viewBox="0 0 24 24" fill="none" stroke="#fff" stroke-width="2"><rect x="6" y="2" width="12" height="20" rx="2"/><line x1="11" y1="18" x2="13" y2="18"/></svg>
        604-947-2164
      </li>
      <li>
        <svg viewBox="0 0 24 24" fill="none" stroke="#fff" stroke-width="2"><circle cx="12" cy="12" r="10"/><path d="M2 12h20M12 2a15 15 0 0 1 0 20M12 2a15 15 0 0 0 0 20"/></svg>
        www.resinworkshub.ca
      </li>
      <li>
        <svg viewBox="0 0 24 24" fill="none" stroke="#fff" stroke-width="2"><rect x="2" y="5" width="20" height="14" rx="1"/><path d="M2 6l10 7 10-7"/></svg>
        ted@resinworkshub.ca
      </li>
    </ul>

    <p class="address">7-4812 Fernhollow Road, Abbotsford, BC, V3K 8R2.</p>
  </section>

  <section class="card card--back" aria-label="Card back">
    <div class="backdrop" role="img" aria-label="Faint repeating brand-mark pattern across the card"></div>
    <div class="brand brand--back"><span class="brand__square"></span>RESINWORKS HUB</div>
  </section>
</main>
</body>
</html>
```